Business Card Design Project

I require a business card with the following information on them for various different people;
name
m:
f:
e:
I have a logo already and will attached that. We are in the construction industry. I require something clean and simple but eye catching at the same time. You can use another colour with our logo if you like and you can style the logo as well if you wish. I am open.
Also it needs to be front and back design.
Industry/Entity Type
Construction
Requirements
Must have
- Logo, name, mobile, fax and email address.
Front and back design

```html
<!DOCTYPE html>
<html lang="en">
<head>
<meta charset="utf-8">
<title>Kestrel Ridge – Business Card</title>
<link rel="stylesheet" href="https://fonts.googleapis.com/css2?family=PT+Sans:wght@400;700&display=swap">
<style>
  :root {
    --backdrop: #b88f22;
    --card-white: #ffffff;
    --card-dark-centre: #5d5d5d;
    --card-dark-edge: #2c2c2c;
    --brand-green: #5bb02f;
    --brand-green-soft: #8cc84a;
    --ink: #222222;
    --wordmark-grey: #4a4a4a;
  }
  * { margin: 0; padding: 0; box-sizing: border-box; }
  html, body {
    width: 1200px;
    height: 686px;
    overflow: hidden;
    background: var(--backdrop);
    font-family: "PT Sans", Arial, sans-serif;
  }
  .canvas {
    position: relative;
    width: 1200px;
    height: 686px;
    background: var(--backdrop);
  }
  .card {
    position: absolute;
    width: 508px;
    height: 290px;
    border-radius: 26px;
    overflow: hidden;
    box-shadow: 0 2px 4px rgba(0, 0, 0, 0.45);
  }
  .card-front {
    left: 73px;
    top: 130px;
    background: var(--card-white);
  }
  .card-back {
    left: 617px;
    top: 271px;
    background: radial-gradient(ellipse at 50% 50%, var(--card-dark-centre) 0%, var(--card-dark-edge) 85%);
  }
  .front-band {
    position: absolute;
    left: 0;
    right: 0;
    bottom: 0;
    height: 70px;
    background: linear-gradient(180deg, var(--brand-green-soft) 0%, var(--brand-green) 100%);
  }
  .brand {
    position: absolute;
    left: 0;
    right: 0;
    display: flex;
    align-items: center;
    justify-content: center;
    gap: 10px;
  }
  .brand-mark {
    display: block;
    background: var(--brand-green);
  }
  .brand-name {
    font-weight: 400;
    line-height: 1;
    white-space: nowrap;
  }
  .card-front .brand { top: 66px; }
  .card-front .brand-mark { width: 28px; height: 28px; }
  .card-front .brand-name { font-size: 38px; color: var(--wordmark-grey); }
  .card-back .brand { top: 112px; gap: 16px; }
  .card-back .brand-mark { width: 50px; height: 50px; }
  .card-back .brand-name { font-size: 62px; color: #ffffff; }
  .contact {
    position: absolute;
    left: 0;
    right: 0;
    top: 142px;
    text-align: center;
    color: var(--ink);
  }
  .contact-name {
    font-size: 16px;
    font-weight: 700;
    color: var(--brand-green);
    margin-bottom: 5px;
  }
  .contact-line {
    display: flex;
    justify-content: center;
    gap: 16px;
    font-size: 13px;
    line-height: 18px;
  }
  .contact-item {
    display: inline-flex;
    align-items: center;
    gap: 2px;
  }
  .contact-icon {
    width: 11px;
    height: 11px;
    fill: var(--brand-green);
  }
</style>
</head>
<body>
<main class="canvas">

  <section class="card card-front" aria-label="Business card front">
    <div class="front-band" role="img" aria-label="Decorative green and steel wave band"></div>

    <div class="brand">
      <span class="brand-mark" aria-hidden="true"></span>
      <span class="brand-name">Kestrel Ridge</span>
    </div>

    <div class="contact">
      <p class="contact-name">Your Name</p>
      <p class="contact-line">
        <span class="contact-item">
          <svg class="contact-icon" viewBox="0 0 12 12" aria-label="Mobile"><path d="M2.5 1 L4.5 1 L5 3.5 L3.8 4.4 C4.5 6 5.9 7.5 7.6 8.2 L8.5 7 L11 7.5 L11 9.5 C11 10.3 10.3 11 9.5 11 C5 10.6 1.4 7 1 2.5 C1 1.7 1.7 1 2.5 1 Z"/></svg>123-456-7890
        </span>
        <span class="contact-item">
          <svg class="contact-icon" viewBox="0 0 12 12" aria-label="Fax"><path d="M3 1 H8 L9 2 V5 H3 Z M1 5.5 H11 V10.5 H1 Z M3 8 H9 V9 H3 Z" fill-rule="evenodd"/></svg>123-456-7890
        </span>
      </p>
      <p class="contact-line">
        <span class="contact-item">
          <svg class="contact-icon" viewBox="0 0 12 12" aria-label="Email"><path d="M1 2.5 H11 V9.5 H1 Z"/><path d="M1.2 2.8 L6 6.4 L10.8 2.8" stroke="#fff" stroke-width="0.9" fill="none"/></svg>name@yourmail.com
        </span>
      </p>
    </div>
  </section>

  <section class="card card-back" aria-label="Business card back">
    <div class="brand">
      <span class="brand-mark" aria-hidden="true"></span>
      <span class="brand-name">Kestrel Ridge</span>
    </div>
  </section>

</main>
</body>
</html>
```